Business Card Design

we are a small based family business that specialise in 12v led lights for velmora caravans.
we also sell 12v switches, wire, circuit breakers, dimmers etc but our main line is LEDs.
We would like something that reflects the LED lighting on our cards.
www.ridgeglowleds.com.au is where you can have a look at to get ideas, of our product.
I have attached the logo we generally use on all our tradix listings and is the main header on our website.

Look forward to seeing what your team comes up with.

Industry/Entity Type

Business

Contact Information for Business Card

Tam 0438 207 915
Quorrin Vale QLD 4399

www.ridgeglowleds.com

```html
<!DOCTYPE html>
<html lang="en">
<head>
<meta charset="utf-8">
<title>Ridgeglow LEDs – Business Card</title>
<link rel="stylesheet" href="https://fonts.googleapis.com/css2?family=Oswald:wght@500;600&family=Exo+2:wght@400;500&display=swap">
<style>
  :root {
    --backdrop: #d9d9d7;
    --card-white: #ffffff;
    --brand-red: #b02a0c;
    --stripe-black: #0d0d0d;
    --ink: #111111;
    --light: #ffffff;
  }
  * { box-sizing: border-box; margin: 0; padding: 0; }
  html, body {
    width: 1200px; height: 933px; overflow: hidden;
    background: var(--backdrop);
  }
  .sheet {
    width: 1200px; height: 933px;
    display: flex; flex-direction: column;
    align-items: center; justify-content: center; gap: 40px;
  }
  .card {
    position: relative;
    width: 700px; height: 400px;
    background: var(--card-white);
    box-shadow: 0 6px 18px rgba(0,0,0,0.18);
    overflow: hidden;
  }
  .card-art { position: absolute; inset: 0; width: 100%; height: 100%; }

  .brand-name {
    position: absolute;
    font-family: "Oswald", sans-serif;
    font-weight: 600;
    color: var(--brand-red);
    text-transform: uppercase;
    letter-spacing: 0.5px;
    line-height: 1;
    white-space: nowrap;
  }
  .card-back .brand-name {
    left: 0; right: 0; top: 170px;
    text-align: center; font-size: 54px;
  }
  .card-front .brand-name {
    left: 60px; top: 128px; font-size: 46px;
  }

  .holder {
    position: absolute; right: 34px; top: 112px;
    text-align: right; color: var(--light);
  }
  .holder-name {
    font-family: "Oswald", sans-serif; font-weight: 500;
    font-size: 40px; letter-spacing: 1px; line-height: 1;
  }
  .holder-role {
    font-family: "Exo 2", sans-serif; font-weight: 500;
    font-size: 13px; letter-spacing: 2px; margin-top: 6px;
  }

  .contacts {
    position: absolute; right: 30px; top: 268px;
    list-style: none;
    font-family: "Exo 2", sans-serif; font-size: 14px;
    color: var(--light);
  }
  .contact {
    display: flex; align-items: center; justify-content: flex-end;
    gap: 8px; height: 24px;
  }
  .contact-icon { width: 16px; height: 16px; flex: none; }
</style>
</head>
<body>
<main class="sheet">

  <section class="card card-back" aria-label="Card back">
    <p class="brand-name">Ridgeglow LEDs</p>
  </section>

  <section class="card card-front" aria-label="Card front">
    <svg class="card-art" viewBox="0 0 700 400" aria-hidden="true">
      <rect width="700" height="400" fill="var(--brand-red)"/>
      <polygon points="0,0 700,232 0,356" fill="var(--stripe-black)"/>
      <polygon points="0,10 682,232 0,346" fill="var(--card-white)"/>
    </svg>

    <p class="brand-name">Ridgeglow LEDs</p>

    <div class="holder">
      <p class="holder-name">TAM</p>
      <p class="holder-role">GENERAL MANAGER</p>
    </div>

    <ul class="contacts">
      <li class="contact">0438 207 915
        <svg class="contact-icon" viewBox="0 0 16 16"><circle cx="8" cy="8" r="8" fill="var(--light)"/><path d="M5 4.5l1.6-.5 1 2.2-1 .8a5 5 0 0 0 2.4 2.4l.8-1 2.2 1-.5 1.6C8 11.5 4.5 8 5 4.5z" fill="var(--brand-red)"/></svg>
      </li>
      <li class="contact">0438 207 916
        <svg class="contact-icon" viewBox="0 0 16 16"><circle cx="8" cy="8" r="8" fill="var(--light)"/><rect x="5.5" y="3.5" width="5" height="9" rx="1" fill="var(--brand-red)"/></svg>
      </li>
      <li class="contact">www.ridgeglowleds.com
        <svg class="contact-icon" viewBox="0 0 16 16"><circle cx="8" cy="8" r="8" fill="var(--light)"/><circle cx="8" cy="8" r="4.2" fill="none" stroke="var(--brand-red)" stroke-width="1.2"/><path d="M3.8 8h8.4M8 3.8v8.4" stroke="var(--brand-red)" stroke-width="1"/></svg>
      </li>
      <li class="contact">tam@ridgeglowleds.com
        <svg class="contact-icon" viewBox="0 0 16 16"><circle cx="8" cy="8" r="8" fill="var(--light)"/><rect x="4" y="5" width="8" height="6" fill="var(--brand-red)"/><path d="M4 5l4 3.2L12 5" fill="none" stroke="var(--light)" stroke-width="0.9"/></svg>
      </li>
      <li class="contact">Quorrin Vale QLD 4399
        <svg class="contact-icon" viewBox="0 0 16 16"><circle cx="8" cy="8" r="8" fill="var(--light)"/><path d="M8 13s-3.3-3.6-3.3-6a3.3 3.3 0 0 1 6.6 0c0 2.4-3.3 6-3.3 6z" fill="var(--brand-red)"/><circle cx="8" cy="7" r="1.2" fill="var(--light)"/></svg>
      </li>
    </ul>
  </section>

</main>
</body>
</html>
```